Create a Wordpress Design (Dorrel)

We need a wordpress design for an established auction and real estate company based in Tennessee. The winning design will incorporate a professional color scheme with company logo in a clean layout. The design needs to consider that this will be developed on a responsive theme. Colors are those that will highlight the logo.
Updates

This client, an older gentleman, wants the site to mimic http://www.quillfordbidhouse.example/. If you can adjust you designs with this site in mind - perhaps 3 columns, less color etc. We are trying to get him a concept that he likes and he keeps mentioning this site. Do not copy this site, but keep it in mind while re-doing the concept. Thanks, - auction services -

Industry/Entity Type

Real Estate

Font styles to use
Sans Serif

Colors

Designer to choose colors to be used in the design.

Requirements
Must have
• - Navigation: 1) Home - with auctions as content as seen at http://brenwickgavel.example/ 2) Properties for Sale 3) Auctions 4) Sell Your Property 5) Community Info 6) About Us 7) Contact Us

Color will be those that highlight logo in a professional creative way. Site tagline: "Our Signs are Everywhere". Site will have a slideshow - please use stock real estate image for the initial photo.

Widgets: 1) social media (FB twitter, linked In, Youtube, RSS) 2) News & Events blog, 3) testimonials 4) featured Property widget.

Footer will have contact info (below) smaller company logo, and the association logos attached, and contact info:
Phone: (615) 555-0178
Contacts: Marion Teague-Hollis
Email: marketing@kenwoodorrel.example
Address: 22-C Elmfield Court W, Murfreesboro, TN 37199

Nice to have
• use and styling of a dropdown menu: Under AUCTIONS, 1) Upcoming 2) Past

```html
<!DOCTYPE html>
<html lang="en">
<head>
<meta charset="utf-8">
<title>Dorrel Commercial — Our Signs are Everywhere</title>
<link href="https://fonts.googleapis.com/css2?family=Arimo:ital,wght@0,400;0,700;1,400&family=Roboto+Condensed:wght@400&display=swap" rel="stylesheet">
<style>
:root{
  --page-bg:#d3d2d2;
  --panel:#ffffff;
  --brand-red:#c4121c;
  --brand-red-dark:#a80e17;
  --nav-active:#cbc7c5;
  --ink:#222222;
  --ink-soft:#333333;
  --bar-dark:#2f2f2f;
  --box-bg:#efefef;
  --box-line:#d6d6d6;
  --footer-grey:#555555;
}
*{box-sizing:border-box;margin:0;padding:0}
html,body{width:900px;height:1200px;overflow:hidden}
body{background:var(--page-bg);font-family:"Arimo",Arial,sans-serif;color:var(--ink);position:relative}
.abs{position:absolute}
.panel{left:75px;top:19px;width:750px;height:1028px;background:var(--panel)}
.brand{left:98px;top:42px;display:flex;align-items:center;gap:8px}
.brand-dot{width:14px;height:14px;border-radius:50%;background:var(--brand-red);flex:none}
.brand-name{font-size:23px;line-height:25px;font-weight:700;color:var(--brand-red)}
.tagline{left:294px;top:60px;font-size:21px;font-variant:small-caps;color:#3a3a3a;letter-spacing:1px}
.social{left:621px;top:61px}
.nav{left:84px;top:130px;width:735px;height:37px;background:var(--brand-red);border-radius:3px;display:flex;list-style:none}
.nav li{color:#fff;font-size:10.5px;font-weight:700;display:flex;align-items:center;justify-content:center;border-right:1px solid var(--brand-red-dark);height:100%}
.nav li:last-child{border-right:none}
.nav li.active{background:var(--nav-active);color:var(--ink)}
.dropdown{left:294px;top:168px;width:137px;list-style:none;box-shadow:0 1px 3px rgba(0,0,0,.3)}
.dropdown li{height:27px;display:flex;align-items:center;padding-left:12px;font-size:11.5px;font-weight:700}
.dropdown .upcoming{background:var(--nav-active);color:var(--ink)}
.dropdown .past{background:var(--brand-red);color:#fff}
.hero{left:86px;top:182px;width:473px;height:240px;border:1px solid #333;background:linear-gradient(180deg,#3f6a3a 0%,#7a3d2a 35%,#8c4a33 65%,#5f8f34 88%,#4a7a2c 100%)}
.side-box{background:var(--box-bg);border:1px solid var(--box-line);border-radius:3px;left:586px;width:225px}
.side-title{position:absolute;left:15px;font-family:"Roboto Condensed",Arial,sans-serif;font-size:23px;font-weight:400;color:#2d2d2d}
.side-text{position:absolute;left:15px;font-size:10px;line-height:13.5px;color:var(--ink-soft);width:195px}
.feat-photo{left:16px;top:73px;width:194px;height:69px;background:linear-gradient(135deg,#6f8d5a,#c9c3b6 50%,#2b2f3a);border:1px solid #fff}
.card{left:87px;width:471px;height:171px;border:1px solid var(--box-line);border-radius:4px;background:linear-gradient(180deg,#f7f7f7,#e7e7e7)}
.card-head{position:absolute;left:7px;top:6px;width:457px;height:25px;background:var(--bar-dark);color:#fff;font-size:12.5px;font-weight:700;padding-left:8px;line-height:25px;letter-spacing:.3px}
.card-photo{left:15px;top:40px;width:135px;height:83px;border:2px solid #cfcfcf;background:linear-gradient(180deg,#8fb0c9 0%,#3f8a6a 35%,#d8d0b8 55%,#2e2e38 100%)}
.card-label{position:absolute;left:161px;top:38px;font-size:11px;font-weight:700;color:var(--brand-red)}
.card-desc{position:absolute;left:161px;top:56px;width:300px;font-size:10px;line-height:13.5px;color:var(--ink)}
.card-meta{position:absolute;left:161px;font-size:10px;color:var(--ink)}
.card-meta b{color:#3a3a55}
.card-action{position:absolute;top:140px;font-size:10.5px;display:flex;align-items:center;gap:5px;color:var(--ink)}
.card-sep{position:absolute;left:78px;top:133px;width:1px;height:22px;background:#cfcfcf}
.bid-btn{position:absolute;left:159px;top:135px;width:202px;height:24px;background:var(--brand-red);border-radius:4px;color:#fff;font-size:10px;font-weight:700;display:flex;align-items:center;justify-content:center}
.testimonial{position:absolute;left:10px;top:62px;width:206px;font-size:10.4px;font-style:italic;line-height:15.2px;color:#444;text-indent:16px}
.quote-mark{position:absolute;font-size:18px;color:#c2c2c2;font-family:Georgia,serif}
.author{position:absolute;right:26px;top:203px;font-size:11px;font-style:italic;color:var(--brand-red)}
.footer-contact{left:75px;top:1073px;font-size:10px;line-height:16.5px;color:#111;font-style:normal}
.badges{left:334px;top:1082px;display:flex;gap:8px;align-items:center}
.badge{background:#2a2a2a}
.footer-brand{left:712px;top:1080px;display:flex;align-items:center;gap:6px}
.footer-brand .brand-dot{background:var(--footer-grey)}
.footer-brand span.name{font-size:14px;line-height:16px;font-weight:700;color:var(--footer-grey)}
.copyright{left:360px;top:1140px;width:460px;text-align:right;font-size:10px;color:#111}
</style>
</head>
<body>
<div class="abs panel"></div>

<header>
  <div class="abs brand"><span class="brand-dot"></span><span class="brand-name">Dorrel<br>Commercial</span></div>
  <div class="abs tagline">Our Signs are Everywhere</div>
  <svg class="abs social" width="195" height="38" viewBox="0 0 195 38" role="img" aria-label="Social media links">
    <circle cx="18" cy="18" r="17" fill="#c4121c"/>
    <circle cx="57" cy="18" r="17" fill="#c4121c"/>
    <circle cx="97" cy="18" r="17" fill="#c4121c"/>
    <circle cx="136" cy="18" r="17" fill="#c4121c"/>
    <circle cx="175" cy="18" r="17" fill="#c4121c"/>
  </svg>
</header>

<nav>
  <ul class="abs nav">
    <li style="width:58px">HOME</li>
    <li style="width:152px">PROPERTIES FOR SALE</li>
    <li class="active" style="width:84px">AUCTIONS</li>
    <li style="width:152px">SELL YOUR PROPERTY</li>
    <li style="width:124px">COMMUNITY INFO</li>
    <li style="width:80px">ABOUT US</li>
    <li style="width:85px">CONTACT US</li>
  </ul>
</nav>

<div class="abs hero" role="img" aria-label="Slideshow photo of a red brick two-storey house with white garage and green lawn"></div>

<ul class="abs dropdown">
  <li class="upcoming">UPCOMING AUCTIONS</li>
  <li class="past">PAST AUCTIONS</li>
</ul>

<aside>
  <section class="abs side-box" style="top:184px;height:238px">
    <h2 class="side-title" style="top:12px">Featured Auction</h2>
    <div class="side-text" style="top:55px;font-weight:700">Multi Estate &amp; Consignment Auction</div>
    <div class="abs feat-photo" role="img" aria-label="Photo of an auctioneer standing in front of a house"></div>
    <div class="side-text" style="top:152px;font-size:9px;line-height:12px"><b>Start Date/ Time:</b> Saturday, April 13,<br>2013 At 10:00 Am</div>
    <div class="side-text" style="top:182px;font-size:9px"><b>Location:</b> 2426 New Harrow,&nbsp; 73899</div>
  </section>

  <section class="abs side-box" style="top:447px;height:238px">
    <h2 class="side-title" style="top:14px">Latest News</h2>
    <div class="side-text" style="top:55px">Kavell KX4T High Lift, 5Series Hartline tractor Kavell KX4T High Lift, 5Series</div>
    <div class="side-text" style="top:108px">Kavell KX4T High Lift, 5Series Hartline tractor Kavell KX4T High Lift, 5Series</div>
    <div class="side-text" style="top:161px">Kavell KX4T High Lift, 5Series Hartline tractor Kavell KX4T High Lift, 5Series</div>
  </section>

  <section class="abs side-box" style="top:710px;height:238px">
    <h2 class="side-title" style="top:10px">Testimonials</h2>
    <span class="quote-mark" style="left:9px;top:46px">&ldquo;</span>
    <p class="testimonial">Lorem Ipsum has been the industry's standard dummy text ever since the 1500s, when an unknown printer took a galley of type and scrambled it to make a type specimen book. It has survived not only five centuries, but also the leap into electronic typesetting, remaining essentially unchanged.</p>
    <span class="quote-mark" style="left:66px;top:182px">&rdquo;</span>
    <div class="author">Wren Ashby</div>
  </section>
</aside>

<main>
  <article class="abs card" style="top:448px">
    <h3 class="card-head">Absolute Auction - Home &amp; 32 Acres</h3>
    <div class="abs card-photo" role="img" aria-label="Photo of a crowd gathered at an on-site house auction"></div>
    <div class="card-label">LIVE ON-SITE AUCTION</div>
    <p class="card-desc">Kavell KX4T High Lift, 500 Series Hartline tractor w/Brayton Loader, Dune buggy, 1408 RT Cutditioner: SHOP &amp;</p>
    <div class="card-meta" style="top:93px"><b>Begins:</b>&nbsp; Saturday, March 16, 2013 at 10:00 AM EDT</div>
    <div class="card-meta" style="top:113px"><b>Location:</b>&nbsp; 7471 Marlow Road Pinecrest, KY 40099</div>
    <div class="card-action" style="left:20px"><svg width="10" height="10" viewBox="0 0 10 10"><circle cx="4" cy="4" r="3" fill="none" stroke="#222" stroke-width="1.6"/><line x1="6.2" y1="6.2" x2="9.3" y2="9.3" stroke="#222" stroke-width="1.8"/></svg>Details</div>
    <span class="card-sep"></span>
    <div class="card-action" style="left:89px"><svg width="14" height="10" viewBox="0 0 14 10"><rect x=".5" y=".5" width="13" height="9" fill="none" stroke="#222"/><path d="M2 8l3-4 2 2 2-3 3 5z" fill="#222"/></svg>Gallery</div>
    <div class="bid-btn">Click here for our online Bidding site</div>
  </article>

  <article class="abs card" style="top:645px">
    <h3 class="card-head">Absolute Auction - Home &amp; 32 Acres</h3>
    <div class="abs card-photo" role="img" aria-label="Photo of a crowd gathered at an on-site house auction"></div>
    <div class="card-label">LIVE ON-SITE AUCTION</div>
    <p class="card-desc">Kavell KX4T High Lift, 500 Series Hartline tractor w/Brayton Loader, Dune buggy, 1408 RT Cutditioner: SHOP &amp;</p>
    <div class="card-meta" style="top:93px"><b>Begins:</b>&nbsp; Saturday, March 16, 2013 at 10:00 AM EDT</div>
    <div class="card-meta" style="top:113px"><b>Location:</b>&nbsp; 7471 Marlow Road Pinecrest, KY 40099</div>
    <div class="card-action" style="left:20px"><svg width="10" height="10" viewBox="0 0 10 10"><circle cx="4" cy="4" r="3" fill="none" stroke="#222" stroke-width="1.6"/><line x1="6.2" y1="6.2" x2="9.3" y2="9.3" stroke="#222" stroke-width="1.8"/></svg>Details</div>
    <span class="card-sep"></span>
    <div class="card-action" style="left:89px"><svg width="14" height="10" viewBox="0 0 14 10"><rect x=".5" y=".5" width="13" height="9" fill="none" stroke="#222"/><path d="M2 8l3-4 2 2 2-3 3 5z" fill="#222"/></svg>Gallery</div>
    <div class="bid-btn">Click here for our online Bidding site</div>
  </article>

  <article class="abs card" style="top:844px">
    <h3 class="card-head">Absolute Auction - Home &amp; 32 Acres</h3>
    <div class="abs card-photo" role="img" aria-label="Photo of a crowd gathered at an on-site house auction"></div>
    <div class="card-label">LIVE ON-SITE AUCTION</div>
    <p class="card-desc">Kavell KX4T High Lift, 500 Series Hartline tractor w/Brayton Loader, Dune buggy, 1408 RT Cutditioner: SHOP &amp;</p>
    <div class="card-meta" style="top:93px"><b>Begins:</b>&nbsp; Saturday, March 16, 2013 at 10:00 AM EDT</div>
    <div class="card-meta" style="top:113px"><b>Location:</b>&nbsp; 7471 Marlow Road Pinecrest, KY 40099</div>
    <div class="card-action" style="left:20px"><svg width="10" height="10" viewBox="0 0 10 10"><circle cx="4" cy="4" r="3" fill="none" stroke="#222" stroke-width="1.6"/><line x1="6.2" y1="6.2" x2="9.3" y2="9.3" stroke="#222" stroke-width="1.8"/></svg>Details</div>
    <span class="card-sep"></span>
    <div class="card-action" style="left:89px"><svg width="14" height="10" viewBox="0 0 14 10"><rect x=".5" y=".5" width="13" height="9" fill="none" stroke="#222"/><path d="M2 8l3-4 2 2 2-3 3 5z" fill="#222"/></svg>Gallery</div>
    <div class="bid-btn">Click here for our online Bidding site</div>
  </article>
</main>

<footer>
  <address class="abs footer-contact">
    Phone: (615) 555-0178<br>
    Contacts: Marion Teague-Hollis<br>
    Email: marketing@kenwoodorrel.example<br>
    Address: 22-C Elmfield Court W,<br>
    Murfreesboro, TN 37199
  </address>
  <div class="abs badges" role="img" aria-label="Association membership badges">
    <span class="badge" style="width:43px;height:36px"></span>
    <span class="badge" style="width:37px;height:28px"></span>
    <span class="badge" style="width:28px;height:28px;border-radius:50%"></span>
    <span class="badge" style="width:28px;height:30px;border-radius:50%"></span>
    <span class="badge" style="width:46px;height:24px"></span>
    <span class="badge" style="width:31px;height:34px;border-radius:50%"></span>
    <span class="badge" style="width:60px;height:26px"></span>
    <span class="badge" style="width:31px;height:36px"></span>
  </div>
  <div class="abs footer-brand"><span class="brand-dot"></span><span class="name">Dorrel<br>Commercial</span></div>
  <p class="abs copyright">Copyright © 2007 - 2014•Dorrel Commercial Realtors, Auctioneers LLC • All Rights Reserved.</p>
</footer>
</body>
</html>
```